Islamic App which helps to calculate, track and pay Sadaqo

We need an application which helps muslim people to calculate and pay Sadaqo - mandatory donations which muslim should pay based on his income. The application will consist of two parts (applications) - the one which is used by "payer" and another one - used by "receiver". To make a payment "payer" will scan QR-code which "receiver" will generate in his app and show to payer. "Receiver" will have option to initiate cash withdrawal once he collected required minimum for the withdrawal.
Important that "payer" side journey to make a payment should be as short as possible - imaging same as you make donation by cash - you just gave money and left, similar experience should be with app - couple-three taps to make it. For receiver side major requirement is to keep the UI/UX as simple as possible, these guys usually are not aware about online payments (roughly speaking this part of the app should be more similar to Quillotap rather than to banking/financial app)
In this Figma I tried to sketch the UX for both sides (just to explain the idea): https://www.plovix.com/file/Rt4mWq8ZpLbN2vKe7sJd3X/Plovix-basics?type=design&node-id=2741-583016&mode=design

Target Market(s)

Muslims

Industry/Entity Type

Donations

Colors
0094D4
00A9DD
6FCCEA
C7EBF8
E9F6FB
00AB8E
00BBA5
67D7C9
C6EFE9
E9F9F6

Requirements
Must have
• The application should have soul. Design should show that this application intend to help people, not just money transfer
Nice to have
• Payment should be as quick as possible, in the sketches I showed it as banknotes/coins which user need to slide-up to pay. Maybe make it similar as Vel OS dock icons?
Should not have
• The application should not look as banking/financial app or wallet app

```html
<!DOCTYPE html>
<html lang="en">
<head>
<meta charset="utf-8">
<title>Sadaqo – app screens</title>
<link rel="stylesheet" href="https://fonts.googleapis.com/css2?family=Gelasio:wght@400;500;600;700&display=swap">
<style>
  :root {
    --page-bg: #ffffff;
    --screen-top: #132a33;
    --screen-bottom: #0e1829;
    --field-green: #0b6b30;
    --code-cell: #103a2d;
    --accent-yellow: #fccb00;
    --arrow-green: #0b7a36;
    --text-light: #ffffff;
    --photo-light: #f3b24a;
    --photo-dark: #3a1f0c;
  }
  * { box-sizing: border-box; margin: 0; padding: 0; }
  html, body { width: 1200px; height: 794px; overflow: hidden; background: var(--page-bg); }
  body { position: relative; font-family: "Gelasio", Georgia, serif; color: var(--text-light); }

  .screen {
    position: absolute; top: 67px; width: 314px; height: 662px;
    border-radius: 34px; overflow: hidden;
    background: linear-gradient(180deg, var(--screen-top) 0%, var(--screen-bottom) 55%, var(--screen-bottom) 100%);
  }
  .screen--signin { left: 67px; }
  .screen--code { left: 442px; }
  .screen--profile { left: 816px; }

  .backdrop-scene {
    position: absolute; left: 0; top: 0; width: 100%; height: 420px;
    background: radial-gradient(ellipse at 50% 50%, rgba(40,70,80,0.35) 0%, rgba(20,40,50,0) 70%);
  }

  .app-name {
    position: absolute; left: 0; width: 100%; text-align: center;
    font-size: 34px; font-weight: 500; color: var(--text-light); line-height: 1;
  }
  .screen--signin .app-name, .screen--code .app-name { top: 176px; }
  .screen--profile .app-name { top: 100px; }
  .screen--profile .app-name { top: 34px; }

  .screen-title {
    position: absolute; left: 0; width: 100%; text-align: center;
    font-size: 19px; font-weight: 500;
  }
  .screen--signin .screen-title { top: 400px; }
  .screen--code .screen-title { top: 333px; }

  .phone-field {
    position: absolute; left: 42px; top: 451px; width: 229px; height: 35px;
    border-radius: 18px; background: var(--field-green);
    font-size: 12px; line-height: 35px; padding-left: 19px;
  }
  .hint { position: absolute; left: 42px; top: 503px; font-size: 10px; }
  .primary-button {
    position: absolute; height: 35px; border-radius: 18px; background: var(--accent-yellow);
    color: var(--field-green); font-size: 14px; font-weight: 600;
    text-align: center; line-height: 35px;
  }
  .screen--signin .primary-button { left: 42px; top: 540px; width: 229px; }
  .screen--code .primary-button { left: 42px; top: 518px; width: 229px; }
  .screen--profile .primary-button { left: 33px; top: 604px; width: 244px; }

  .code-cells { position: absolute; left: 58px; top: 393px; display: flex; gap: 15px; }
  .code-cell { width: 38px; height: 35px; background: var(--code-cell); border-radius: 2px; }
  .sms-note {
    position: absolute; left: 0; top: 448px; width: 100%; text-align: center;
    font-size: 10px; line-height: 19px;
  }

  .recipient-photo {
    position: absolute; left: 14px; top: 100px; width: 282px; height: 360px; border-radius: 18px;
    background: radial-gradient(ellipse at 55% 25%, #ffe7a8 0%, var(--photo-light) 25%, #a05a1c 60%, var(--photo-dark) 100%);
  }
  .next-arrow { position: absolute; left: 273px; top: 263px; }
  .recipient-name { position: absolute; left: 33px; top: 484px; font-size: 27px; font-weight: 500; }
  .recipient-story { position: absolute; left: 33px; top: 529px; font-size: 12px; }
  .balance { position: absolute; left: 33px; top: 555px; font-weight: 700; }
  .balance__amount { font-size: 28px; color: var(--accent-yellow); }
  .balance__currency { font-size: 15px; font-weight: 400; color: var(--text-light); margin-left: 2px; }
</style>
</head>
<body>

  <section class="screen screen--signin">
    <div class="backdrop-scene" role="img" aria-label="Faint night scene of a mosque silhouette under a crescent moon"></div>
    <div class="app-name">Sadaqo</div>
    <h1 class="screen-title">Sign In To Sadaqo</h1>
    <div class="phone-field">+ 971 (50) 000-00-00</div>
    <p class="hint">Please enter your UAE phone number</p>
    <div class="primary-button">Next</div>
  </section>

  <section class="screen screen--code">
    <div class="backdrop-scene" role="img" aria-label="Faint night scene of a mosque silhouette under a crescent moon"></div>
    <div class="app-name">Sadaqo</div>
    <h1 class="screen-title">Input Code</h1>
    <div class="code-cells">
      <div class="code-cell"></div><div class="code-cell"></div>
      <div class="code-cell"></div><div class="code-cell"></div>
    </div>
    <p class="sms-note">We have sent an SMS with a 4 digit code to<br>phone +971 50 7284619</p>
    <div class="primary-button">Sign In</div>
  </section>

  <section class="screen screen--profile">
    <div class="app-name">Sadaqo</div>
    <div class="recipient-photo" role="img" aria-label="Photo of sunlit mosque arches with palm trees beyond"></div>
    <svg class="next-arrow" width="34" height="34" viewBox="0 0 34 34" aria-hidden="true">
      <circle cx="17" cy="17" r="17" fill="#0b7a36"/>
      <path d="M12 12 L16 17 L12 22 M17 12 L21 17 L17 22" fill="none" stroke="#fccb00" stroke-width="2" stroke-linecap="round" stroke-linejoin="round"/>
    </svg>
    <h2 class="recipient-name">Hamdan</h2>
    <p class="recipient-story">I am from Pakistan. I have three kids.</p>
    <p class="balance"><span class="balance__amount">847</span><span class="balance__currency">AED</span></p>
    <div class="primary-button">Withdraw Money</div>
  </section>

</body>
</html>
```